Black Matte card with samurai logo which I would like it to be textured and company name on one side and on the other side I would like the company information with the reno (Face logo) Sushi logo. Double Sided card.

majority customers are University students, University sororities and fraternities.

It Company

Reno Sushi
317 W. Harlow Ave
Tucson, AZ 85042
Phone (520)413-6271
Fax (520)357-1846
E-mail: Renosushidesert@mailbox-example.com
FB: Renosushidesert
Twitter: Renosushidesert

• Present Normal

```html
<!DOCTYPE html>
<html lang="en">
<head>
<meta charset="utf-8">
<title>Reno Sushi – Business Card</title>
<link rel="stylesheet" href="https://fonts.googleapis.com/css2?family=Economica:wght@400&display=swap">
<style>
  :root {
    --page: #ffffff;
    --card: #070808;
    --ink: #f4f4f4;
    --rule: #9e1116;
  }
  html, body {
    margin: 0;
    padding: 0;
    width: 1200px;
    height: 702px;
    overflow: hidden;
    background: var(--page);
  }
  .card {
    position: absolute;
    left: 44px;
    top: 43px;
    width: 1112px;
    height: 616px;
    background: var(--card);
    font-family: "Economica", sans-serif;
    font-weight: 400;
    color: var(--ink);
    white-space: nowrap;
  }
  .brand {
    position: absolute;
    left: 194px;
    top: 318px;
    width: 345px;
    height: 52px;
    margin: 0;
    text-align: center;
    font-size: 44px;
    font-weight: 400;
    line-height: 52px;
    letter-spacing: 0.5px;
  }
  .divider {
    position: absolute;
    left: 742px;
    top: 294px;
    width: 5px;
    height: 296px;
    background: var(--rule);
  }
  .contact {
    position: absolute;
    left: 774px;
    top: 309px;
  }
  .contact-name {
    margin: 0;
    font-size: 34px;
    font-weight: 400;
    line-height: 40px;
  }
  .contact-address {
    margin: 0;
    font-size: 22px;
    line-height: 26px;
    font-style: normal;
  }
  .contact-lines {
    list-style: none;
    margin: 38px 0 0;
    padding: 0;
    font-size: 22px;
    line-height: 30px;
  }
</style>
</head>
<body>
  <main class="card">
    <p class="brand">Reno Sushi</p>

    <div class="divider" aria-hidden="true"></div>

    <section class="contact">
      <h1 class="contact-name">Reno Sushi</h1>
      <address class="contact-address">317 W. Harlow Ave Tucson, AZ 85042</address>
      <ul class="contact-lines">
        <li>Phone (520)413-6271</li>
        <li>Fax (520)357-1846</li>
        <li>E-mail: Renosushidesert@mailbox-example.com</li>
        <li>FB: Renosushidesert</li>
        <li>Twitter: Renosushidesert</li>
      </ul>
    </section>
  </main>
</body>
</html>
```